Store Promo Card (already have logo!)

I need a card design (single side) for my online women’s gift shop containing a promotional code to be placed in bags for attendees at an event. I’m flexible on both shape and sizing, but perhaps a 4x6 card.
—It should contain my attached logo, my website (www.brivelhome.com), and my Instagram handle (@brivelhome) and promotion language such as “15% off your purchase with code: PELVON”.
—I think I would like my logo to be large.
—It should be clean, simple and modern in design and should use the colors from my logo.
—I would like about 3-5 product pictures depending on design.
Target Market(s)
Women ages 30 to 60
Industry/Entity Type
Retail Upscale Gift

```html
<!DOCTYPE html>
<html lang="en">
<head>
<meta charset="utf-8">
<title>Brivel Home – Promo Card</title>
<link href="https://fonts.googleapis.com/css2?family=Abril+Fatface&family=Playfair+Display:wght@400;700&display=swap" rel="stylesheet">
<style>
  :root {
    --page-bg: #efefef;
    --card-pink: #f2dcd6;
    --ink: #6a6766;
    --rule: #8a8685;
  }
  * { margin: 0; padding: 0; box-sizing: border-box; }
  html, body {
    width: 1200px;
    height: 800px;
    overflow: hidden;
    background: var(--page-bg);
  }
  .canvas {
    position: relative;
    width: 1200px;
    height: 800px;
  }
  .promo-card {
    position: absolute;
    left: 370px;
    top: 20px;
    width: 460px;
    height: 760px;
    background: var(--card-pink);
    border-radius: 48px;
    color: var(--ink);
  }
  .frame {
    position: absolute;
    left: 45px;
    width: 370px;
    border: 1.5px solid var(--rule);
    text-align: center;
  }
  .frame-label {
    position: absolute;
    left: 50%;
    bottom: 0;
    transform: translate(-50%, 50%);
    background: var(--card-pink);
    padding: 0 14px;
    white-space: nowrap;
    line-height: 1;
  }

  /* Brand name block */
  .brand-frame {
    top: 44px;
    height: 160px;
    display: flex;
    align-items: center;
    justify-content: center;
  }
  .brand-name {
    font-family: "Abril Fatface", serif;
    font-size: 40px;
    letter-spacing: 1px;
    line-height: 1;
  }

  /* Offer block */
  .offer-frame { top: 240px; height: 290px; }
  .offer-amount {
    font-family: "Abril Fatface", serif;
    font-size: 104px;
    line-height: 0.92;
    margin-top: 30px;
  }
  .offer-terms {
    font-family: "Playfair Display", serif;
    font-weight: 700;
    font-size: 19px;
    margin-top: 22px;
  }
  .promo-code {
    font-family: "Playfair Display", serif;
    font-weight: 700;
    font-size: 34px;
    letter-spacing: 2px;
  }

  /* Contact block */
  .contact-frame { top: 575px; height: 135px; }
  .website {
    font-family: "Playfair Display", serif;
    font-weight: 400;
    font-size: 30px;
    margin-top: 40px;
  }
  .social-handle {
    font-family: "Playfair Display", serif;
    font-size: 22px;
    display: inline-flex;
    align-items: center;
    gap: 10px;
  }
  .handle-dot {
    width: 18px;
    height: 18px;
    border: 2px solid var(--ink);
    border-radius: 50%;
  }
</style>
</head>
<body>
<main class="canvas">
  <section class="promo-card">
    <div class="frame brand-frame">
      <div class="brand-name">BRIVEL HOME</div>
    </div>

    <div class="frame offer-frame">
      <div class="offer-amount">15%<br>OFF</div>
      <p class="offer-terms">your purchase with code:</p>
      <div class="frame-label promo-code">PELVON</div>
    </div>

    <div class="frame contact-frame">
      <div class="website">www.brivelhome.com</div>
      <div class="frame-label social-handle"><span class="handle-dot"></span>@brivelhome</div>
    </div>
  </section>
</main>
</body>
</html>
```